Need a Wordpress website for my HVAC company

I need a Wordpress website created for an HVAC company in a competitive market.
Following are some websites I like:
My current website is www.borvicoheating.com - we also have a facebook page with some pictures

We are an airconditioning and heating company that does both residential and commmercial work.
We need the following info on our website:
-mobile friendly
-Schedule an appt -repair/maintnenace/installation (i would like this option to always be on the page even if they scroll down.)
-24 hour service
-coupons /promotions
-financing
-reviews/testimonials
-about
-blog
-Our service area
The following are services we provide:
-Air conditioning - Installation/Service/Maintenance/new construction
-Heating - Installation/Service/Maintenance/new construction ( gas furnace, 2 stage furnace, electric heat)
-Duct - Repair/Replacement/Istallation - (zone systems)
-thermostats (wifi)
-Heat pump
-Air handler
-self communicating systems
-carbon monoxide testing
-hail damage
-duct sealing
-insulation
-Air cleaners - UV Air purifiers
-humidifiers

I would also like Quilbo SEO add on

Target Market(s)

Anyone who needs our services HVAC contractor

Industry/Entity Type

Hvac

Contact Information for Business Card

Phone:480-555-2046
website:www.borvicoheating.com
email pmarsh@borvicoheating.com

Coding

Coded - Design and coding required

Number of Pages Required

5+ page

Font styles to use
Serif
Sans Serif

Requirements
Must have
• I wrote in brief. I already have Webly Nest. Long story I paid for 3 years already. I need someone to put website there. Ive never used Wordpress but would like a template page so I can easily add services.
Nice to have
• Clean, bright, original

```html
<!DOCTYPE html>
<html lang="en">
<head>
<meta charset="utf-8">
<title>Borvico Mechanical Services – Heating &amp; Cooling</title>
<link href="https://fonts.googleapis.com/css2?family=PT+Sans:wght@400;700&display=swap" rel="stylesheet">
<style>
:root{
  --brand:#1b4f86;
  --brand-dark:#153f6c;
  --ink:#2b2b2b;
  --muted:#7a7a7a;
  --band:#f3f3f3;
  --footer:#f5f5f5;
  --line:#dcdcdc;
  --white:#ffffff;
}
*{margin:0;padding:0;box-sizing:border-box}
html,body{width:1200px;height:3130px;overflow:hidden}
body{font-family:"PT Sans",Arial,sans-serif;color:var(--ink);background:var(--white);position:relative}
.abs{position:absolute}
section,header,footer{position:absolute;left:0;width:1200px}
a{color:inherit;text-decoration:none}
.btn{position:absolute;background:var(--brand);color:var(--white);font-weight:700;text-transform:uppercase;display:flex;align-items:center;justify-content:center;border-radius:2px}
.body-text{font-size:13px;line-height:25px;color:var(--muted)}
.img-fill{position:absolute}

/* header + hero */
.hero{top:0;height:574px;background:radial-gradient(ellipse at 60% 45%,#ffffff 0%,#f7f7f7 55%,#ececec 100%)}
.brand-mark{position:absolute;left:131px;top:28px;display:flex;align-items:center;gap:10px}
.brand-mark .dot{width:26px;height:26px;border-radius:50%;background:var(--brand)}
.brand-mark span{font-size:30px;font-weight:700;color:var(--brand)}
.support{position:absolute;right:130px;top:34px;display:flex;align-items:center;gap:14px;font-size:15px}
.support b{color:var(--brand)}
.support .phone-ring{width:30px;height:30px;border:1.5px solid var(--brand);border-radius:50%;display:flex;align-items:center;justify-content:center}
.main-nav{position:absolute;right:130px;top:90px;display:flex;gap:47px;font-size:12px;text-transform:uppercase;color:#444}
.main-nav .active{color:var(--brand)}
.hero-kicker{left:131px;top:236px;font-size:29px;letter-spacing:.5px}
.hero-title{left:131px;top:284px;font-size:43px;font-weight:700;letter-spacing:.5px;white-space:nowrap}
.hero-visual{left:570px;top:222px;width:586px;height:228px;border-radius:90px 70px 24px 24px / 80px 60px 24px 24px;background:linear-gradient(180deg,#3f7fcf 0%,#2a63b0 55%,#1f4a8a 82%,#2a2f3d 100%);box-shadow:0 14px 18px -10px rgba(0,0,0,.35)}
.slider-dots{display:flex;gap:6px}
.slider-dots i{width:10px;height:10px;border-radius:50%;background:#cfcfcf;display:block}
.slider-dots i.on{background:var(--brand)}

/* welcome */
.welcome{top:574px;height:484px}
.section-title{position:absolute;font-size:31px;letter-spacing:.5px;font-weight:400}
.section-title b{font-weight:700}
.checklist{list-style:none;position:absolute;left:131px;top:212px}
.checklist li{display:flex;align-items:center;gap:18px;font-size:14px;height:29.5px;color:#444}
.checklist svg{flex:none}
.video-frame{position:absolute;left:597px;top:94px;width:469px;height:288px;border:1px solid var(--line);padding:8px;background:var(--white)}

/* service bands */
.residential{top:1058px;height:459px;background:var(--band)}
.commercial{top:1517px;height:441px;background:var(--white)}
.service-row{position:absolute;display:flex;gap:22px;align-items:center}
.service-row div{display:flex;align-items:center;gap:14px;font-size:19px;text-transform:uppercase;margin-right:10px}
.ring{width:54px;height:54px;border:2px solid var(--brand);border-radius:50%;display:flex;align-items:center;justify-content:center}

/* why */
.why{top:1958px;height:463px;background:var(--band)}
.feature{position:absolute;width:300px}
.feature h3{position:absolute;left:56px;top:0;font-size:19px;font-weight:400;text-transform:uppercase;white-space:nowrap}
.feature p{position:absolute;left:56px;top:34px;width:245px;font-size:12.5px;line-height:29px;color:var(--muted)}
.feature svg{position:absolute;left:0;top:0}

/* testimonials */
.reviews{top:2421px;height:338px}
.quote-text{position:absolute;left:262px;top:126px;width:676px;text-align:center;font-size:12px;line-height:25px;color:var(--muted)}
.reviewer{position:absolute;left:0;width:1200px;top:225px;text-align:center;font-size:13px;font-style:italic;color:var(--brand)}

/* footer */
.site-footer{top:2759px;height:371px;background:var(--footer)}
.footer-head{position:absolute;font-size:19px;text-transform:uppercase;top:47px}
.quick-links{position:absolute;left:440px;top:92px;list-style:none;font-size:11.5px;color:#555}
.quick-links li{height:24px}
.contact-list{position:absolute;left:647px;top:92px;list-style:none;font-size:11.5px;color:#555}
.contact-list li{display:flex;gap:14px;height:27px;align-items:flex-start}
.social{position:absolute;left:887px;top:94px;display:flex;gap:7px}
.social i{width:31px;height:31px;border:1.5px solid #777;border-radius:50%;display:block}
.cards{position:absolute;left:887px;top:202px;display:flex;gap:5px}
.cards i{width:25px;height:15px;border-radius:2px;display:block}
.copyright{position:absolute;left:0;width:1200px;top:335px;text-align:center;font-size:11.5px;color:#444}
</style>
</head>
<body>

<section class="hero">
  <div class="brand-mark"><div class="dot"></div><span>Borvico</span></div>
  <div class="support">
    <b>24/7 CUSTOMER SUPPORT</b>
    <div class="phone-ring"><svg width="14" height="14" viewBox="0 0 24 24"><path d="M6.6 10.8a15 15 0 0 0 6.6 6.6l2.2-2.2a1 1 0 0 1 1-.25 11 11 0 0 0 3.6.6 1 1 0 0 1 1 1V20a1 1 0 0 1-1 1A17 17 0 0 1 3 4a1 1 0 0 1 1-1h3.5a1 1 0 0 1 1 1 11 11 0 0 0 .6 3.6 1 1 0 0 1-.25 1z" fill="#1b4f86"/></svg></div>
    <span>(480) 555-2046</span>
  </div>
  <nav class="main-nav">
    <a class="active">Home</a><a>About us</a><a>24 hour services</a><a>Coupons</a><a>Reviews</a><a>Blog</a><a>Contact us</a>
  </nav>
  <div class="abs hero-kicker">REPAIR &amp; MAINTENANCE</div>
  <h1 class="abs hero-title">AIR CONDITIONING</h1>
  <a class="btn" style="left:131px;top:372px;width:238px;height:48px;font-size:13px">Schedule an appointment</a>
  <div class="abs slider-dots" style="left:131px;top:462px"><i class="on"></i><i></i><i></i></div>
  <div class="img-fill hero-visual" role="img" aria-label="Branded service van with a technician giving a thumbs up"></div>
</section>

<section class="welcome">
  <h2 class="section-title" style="left:131px;top:94px">WELCOME TO <b>BORVICO</b></h2>
  <p class="abs body-text" style="left:131px;top:147px;width:430px">Borvico Mechanical Services offers many different financing plans. The top reasons to finance with us are:</p>
  <ul class="checklist">
    <li><svg width="13" height="13" viewBox="0 0 14 14"><circle cx="7" cy="7" r="7" fill="#1b4f86"/><path d="M5 4l3 3-3 3" stroke="#fff" stroke-width="1.8" fill="none"/></svg>Low cost same as cash financing for qualifying customers.</li>
    <li><svg width="13" height="13" viewBox="0 0 14 14"><circle cx="7" cy="7" r="7" fill="#1b4f86"/><path d="M5 4l3 3-3 3" stroke="#fff" stroke-width="1.8" fill="none"/></svg>Fast and easy application.</li>
    <li><svg width="13" height="13" viewBox="0 0 14 14"><circle cx="7" cy="7" r="7" fill="#1b4f86"/><path d="M5 4l3 3-3 3" stroke="#fff" stroke-width="1.8" fill="none"/></svg>Monthly payments as low as $56.90 per month.</li>
    <li><svg width="13" height="13" viewBox="0 0 14 14"><circle cx="7" cy="7" r="7" fill="#1b4f86"/><path d="M5 4l3 3-3 3" stroke="#fff" stroke-width="1.8" fill="none"/></svg>No lien on your home</li>
  </ul>
  <a class="btn" style="left:131px;top:346px;width:96px;height:38px;font-size:11px">Read more</a>
  <div class="video-frame">
    <div class="img-fill" role="img" aria-label="Technician on a ladder installing a wall air conditioner" style="left:8px;top:8px;width:451px;height:270px;background:linear-gradient(135deg,#d9d9d7 0%,#c4c2bd 55%,#a9a59c 100%)"></div>
    <svg class="abs" style="left:199px;top:108px" width="72" height="72" viewBox="0 0 72 72"><circle cx="36" cy="36" r="33" fill="rgba(80,80,80,.55)" stroke="#fff" stroke-width="3"/><path d="M28 22l22 14-22 14z" fill="#fff"/></svg>
  </div>
</section>

<section class="residential">
  <div class="img-fill" role="img" aria-label="Wall mounted split air conditioner and a hand holding a remote" style="left:0;top:0;width:480px;height:459px;background:linear-gradient(120deg,#e4e4e4 0%,#f7f7f7 55%,#ececec 100%)"></div>
  <h2 class="section-title" style="left:515px;top:68px">RESIDENTIAL</h2>
  <p class="abs body-text" style="left:515px;top:130px;width:560px">Borvico Mechanical Services is the premier residential heating, air conditioning, and energy solutions provider in the greater Phoenix area. We can help you lower your energy bills, reduce your environmental impact, and increase the comfort of your home.</p>
  <div class="service-row" style="left:512px;top:234px">
    <div><span class="ring"><svg width="26" height="26" viewBox="0 0 24 24"><path d="M21 6.5a5 5 0 0 1-6.6 4.7L6 19.6a2 2 0 0 1-2.8-2.8l8.4-8.4A5 5 0 0 1 17.5 3l-3 3 .6 2.9 2.9.6z" fill="#1b4f86"/></svg></span>Repair</div>
    <div><span class="ring"><svg width="28" height="28" viewBox="0 0 24 24"><circle cx="9" cy="10" r="4.5" fill="none" stroke="#1b4f86" stroke-width="2.2" stroke-dasharray="2.4 1.2"/><circle cx="9" cy="10" r="1.6" fill="#1b4f86"/><circle cx="17" cy="17" r="3" fill="none" stroke="#1b4f86" stroke-width="1.8" stroke-dasharray="1.6 1"/></svg></span>Maintenance</div>
    <div><span class="ring"><svg width="26" height="26" viewBox="0 0 24 24"><path d="M3 10h4v11H3zM9 10l4-7a2 2 0 0 1 3 2l-1 4h5a2 2 0 0 1 2 2.4l-1.6 7A2 2 0 0 1 18.4 21H9z" fill="none" stroke="#1b4f86" stroke-width="1.8"/></svg></span>Installation</div>
  </div>
  <a class="btn" style="left:517px;top:338px;width:96px;height:40px;font-size:11px">Read more</a>
</section>

<section class="commercial">
  <h2 class="section-title" style="left:131px;top:122px">COMMERCIAL</h2>
  <p class="abs body-text" style="left:131px;top:172px;width:560px">Borvico Mechanical Services is the premier residential heating, air conditioning, and energy solutions provider in the greater Phoenix area. We can help you lower your energy bills, reduce your environmental impact, and increase the comfort of your home.</p>
  <div class="service-row" style="left:131px;top:270px">
    <div><span class="ring"><svg width="26" height="26" viewBox="0 0 24 24"><path d="M21 6.5a5 5 0 0 1-6.6 4.7L6 19.6a2 2 0 0 1-2.8-2.8l8.4-8.4A5 5 0 0 1 17.5 3l-3 3 .6 2.9 2.9.6z" fill="#1b4f86"/></svg></span>Repair</div>
    <div><span class="ring"><svg width="28" height="28" viewBox="0 0 24 24"><circle cx="9" cy="10" r="4.5" fill="none" stroke="#1b4f86" stroke-width="2.2" stroke-dasharray="2.4 1.2"/><circle cx="9" cy="10" r="1.6" fill="#1b4f86"/><circle cx="17" cy="17" r="3" fill="none" stroke="#1b4f86" stroke-width="1.8" stroke-dasharray="1.6 1"/></svg></span>Maintenance</div>
    <div><span class="ring"><svg width="26" height="26" viewBox="0 0 24 24"><path d="M3 10h4v11H3zM9 10l4-7a2 2 0 0 1 3 2l-1 4h5a2 2 0 0 1 2 2.4l-1.6 7A2 2 0 0 1 18.4 21H9z" fill="none" stroke="#1b4f86" stroke-width="1.8"/></svg></span>Installation</div>
  </div>
  <a class="btn" style="left:131px;top:365px;width:96px;height:40px;font-size:11px">Read more</a>
  <div class="img-fill" role="img" aria-label="Smiling technician in a plaid shirt carrying an air conditioner unit" style="left:710px;top:38px;width:490px;height:403px;background:linear-gradient(160deg,#f1e6d8 0%,#c9a27a 35%,#4d6a8c 70%,#e9e9e9 100%)"></div>
</section>

<section class="why">
  <h2 class="section-title" style="left:0;width:1200px;text-align:center;top:76px">WHY CHOOSE US</h2>

  <div class="feature" style="left:131px;top:179px">
    <svg width="30" height="30" viewBox="0 0 24 24"><circle cx="12" cy="12" r="9.5" fill="none" stroke="#1b4f86" stroke-width="2.4"/><path d="M12 7v5l3.5 2" stroke="#1b4f86" stroke-width="2" fill="none"/></svg>
    <h3>24/7 Emergency Service</h3><p>You need air conditioning service when you need it, not when we feel like being open.</p>
  </div>
  <div class="feature" style="left:459px;top:179px">
    <svg width="30" height="30" viewBox="0 0 24 24"><rect x="3" y="5" width="18" height="16" fill="none" stroke="#1b4f86" stroke-width="2"/><rect x="3" y="5" width="18" height="4" fill="#1b4f86"/><path d="M6 12h2M11 12h2M16 12h2M6 16h2M11 16h2M16 16h2" stroke="#1b4f86" stroke-width="2"/></svg>
    <h3>Same Day Service</h3><p>You need air conditioning service when you need it, not when we feel like being open.</p>
  </div>
  <div class="feature" style="left:789px;top:179px">
    <svg width="30" height="30" viewBox="0 0 24 24"><path d="M21 6.5a5 5 0 0 1-6.6 4.7L6 19.6a2 2 0 0 1-2.8-2.8l8.4-8.4A5 5 0 0 1 17.5 3l-3 3 .6 2.9 2.9.6z" fill="#1b4f86"/></svg>
    <h3>Trained Technicians</h3><p>You need air conditioning service when you need it, not when we feel like being open.</p>
  </div>
  <div class="feature" style="left:131px;top:308px">
    <svg width="30" height="30" viewBox="0 0 24 24"><path d="M14 2L5 14h6l-2 8 9-12h-6z" fill="#1b4f86"/></svg>
    <h3>Free Energy Survey</h3><p>You need air conditioning service when you need it, not when we feel like being open.</p>
  </div>
  <div class="feature" style="left:459px;top:308px">
    <svg width="30" height="30" viewBox="0 0 24 24"><rect x="2" y="5" width="20" height="14" rx="2" fill="none" stroke="#1b4f86" stroke-width="2"/><rect x="2" y="9" width="20" height="3" fill="#1b4f86"/></svg>
    <h3>Pay By The Job</h3><p>You need air conditioning service when you need it, not when we feel like being open.</p>
  </div>
  <div class="feature" style="left:789px;top:308px">
    <svg width="30" height="30" viewBox="0 0 24 24"><path d="M12 2L2 7h20z" fill="#1b4f86"/><path d="M4 9h2v9H4zM9 9h2v9H9zM13 9h2v9h-2zM18 9h2v9h-2zM2 19h20v3H2z" fill="#1b4f86"/></svg>
    <h3>Fairness and Honesty</h3><p>You need air conditioning service when you need it, not when we feel like being open.</p>
  </div>
</section>

<section class="reviews">
  <h2 class="section-title" style="left:0;width:1200px;text-align:center;top:50px">OUR CUSTOMERS SAY...</h2>
  <svg class="abs" style="left:178px;top:126px" width="52" height="34" viewBox="0 0 52 34"><path d="M10 0h14L12 34H0zM34 0h14L36 34H24z" fill="#cfcfcf"/></svg>
  <p class="quote-text">Nemo enim ipsam voluptatem quia voluptas sit aspernatur aut odit aut fugit, sed quia consequuntur magni dolores eos qui ratione voluptatem sequi nesciunt. Neque porro quisquam est, qui dolorem ipsum quia dolor sit amet, consectetur, adipisci velit, sed quia non numquam eius modi tempora incidunt ut labore et dolore magnam aliquam quaerat voluptatem.</p>
  <div class="reviewer">- Dana Reyes -</div>
  <div class="abs slider-dots" style="left:578px;top:280px"><i class="on"></i><i></i><i></i></div>
</section>

<footer class="site-footer">
  <div class="brand-mark" style="top:75px"><div class="dot"></div><span>Borvico</span></div>

  <div class="footer-head" style="left:440px">Quick links</div>
  <ul class="quick-links">
    <li>Home</li><li>About us</li><li>24 hour services</li><li>Coupons</li><li>Financing</li><li>Reviews</li><li>Blog</li><li>Contact us</li>
  </ul>

  <div class="footer-head" style="left:647px">Contact us</div>
  <ul class="contact-list">
    <li><svg width="12" height="12" viewBox="0 0 24 24"><path d="M6.6 10.8a15 15 0 0 0 6.6 6.6l2.2-2.2a1 1 0 0 1 1-.25 11 11 0 0 0 3.6.6 1 1 0 0 1 1 1V20a1 1 0 0 1-1 1A17 17 0 0 1 3 4a1 1 0 0 1 1-1h3.5a1 1 0 0 1 1 1 11 11 0 0 0 .6 3.6 1 1 0 0 1-.25 1z" fill="#555"/></svg>201-555-0187</li>
    <li><svg width="12" height="12" viewBox="0 0 24 24"><rect x="3" y="8" width="18" height="10" fill="#555"/><rect x="7" y="3" width="10" height="5" fill="#555"/><rect x="7" y="15" width="10" height="6" fill="#fff" stroke="#555" stroke-width="2"/></svg>201-555-0187</li>
    <li><svg width="12" height="12" viewBox="0 0 24 24"><rect x="2" y="5" width="20" height="14" fill="#555"/><path d="M2 5l10 8 10-8" stroke="#fff" stroke-width="1.6" fill="none"/></svg><u>info@borvicoheating.com</u></li>
    <li style="height:40px"><svg width="12" height="12" viewBox="0 0 24 24"><path d="M12 2a7 7 0 0 0-7 7c0 5 7 13 7 13s7-8 7-13a7 7 0 0 0-7-7zm0 9.5A2.5 2.5 0 1 1 12 6.5a2.5 2.5 0 0 1 0 5z" fill="#555"/></svg><span style="width:160px;line-height:15px">#2868 Lorem ipsum dolor sit amet, consectetur</span></li>
  </ul>

  <div class="footer-head" style="left:887px">Follow us</div>
  <div class="social" aria-label="Social profiles"><i></i><i></i><i></i><i></i><i></i></div>
  <div class="footer-head" style="left:887px;top:162px">We accept</div>
  <div class="cards" aria-label="Accepted payment cards"><i style="background:#e08a3c"></i><i style="background:#2f6db5"></i><i style="background:#d9534f"></i><i style="background:#4a90c8"></i></div>

  <div class="abs" style="left:131px;top:314px;width:938px;height:1px;background:var(--line)"></div>
  <div class="copyright">© 2016 borvicoheating.com. All rights reserved.</div>
</footer>

</body>
</html>
```